Brochure for a website accessibility report

This brochure is related to a report that www.qelvantrix.org sell. The report shows the results of an automated audit of a websites accessibility. It shows details of issues found with screen shots, examples of code and provides remediation advice.

The brochure will be a pdf 8.5 inches by 11 inches. It can be anywhere from 6 to 10 pages.

The FlintVue™ name itself should be “Bree Serif” font. The fonts, styles, colors and sizes are up to you.

The images used and logo of the Office of Digital Reachworks and K7P logo are upload

We highlighted in blue page extracts from the report we sell. Do not use the blue highlight, it is merely there to show you where the specific examples of the report we sell are vs the other content in the report. The areas in blue which show the content from the actual report should be shown as an extract of the actual page of the report. You have flexibility to change the layout and the way the content look.

The red square callouts over the blue content are callouts that describe the specific page extracts. We used it as a red callout only so that you would be able to see it. You should change the specific location, look and feel of the callout to be appropriate

Target Market(s)

Marketing and Technical people

Industry/Entity Type

Information Technology

Font styles to use
Sans Serif

Colors

Designer to choose colors to be used in the design.

Requirements
Should not have
• wheelchairs, images of blind people

```html
<!DOCTYPE html>
<html lang="en">
<head>
<meta charset="utf-8">
<title>Accessibility Report Brochure – Covers</title>
<link rel="stylesheet" href="https://fonts.googleapis.com/css2?family=Roboto+Slab:wght@400;700&family=Montserrat:wght@300;400&display=swap">
<style>
  :root {
    --backdrop: #dcdcdf;
    --paper: #f4f4f4;
    --green: #23a566;
    --ink-dark: #2f2f2f;
    --grey-deep: #3c3c3c;
    --grey-mid: #6b6b6b;
    --grey-light: #cfcfcf;
    --white: #ffffff;
  }
  * { margin: 0; padding: 0; box-sizing: border-box; }
  html, body { width: 1200px; height: 900px; overflow: hidden; }
  body { background: var(--backdrop); position: relative; font-family: "Montserrat", sans-serif; }

  .spread {
    position: absolute; left: 42px; top: 50px;
    width: 1116px; height: 800px;
    background: var(--paper);
    box-shadow: 0 6px 24px rgba(0,0,0,0.18);
  }
  .spread-art { position: absolute; inset: 0; }

  .contact { position: absolute; left: 67px; top: 618px; color: var(--white); }
  .contact-title { font-weight: 300; font-size: 20px; letter-spacing: 4px; margin-bottom: 8px; }
  .contact-lines { font-size: 10.5px; line-height: 15px; font-weight: 400; opacity: .92; }
  .contact-lines + .contact-lines { margin-top: 10px; }
  .contact-web { position: absolute; left: 332px; top: 737px; color: var(--white); font-size: 10.5px; }

  .report-title {
    position: absolute; left: 590px; top: 650px;
    font-family: "Roboto Slab", serif; font-weight: 400;
    font-size: 54px; letter-spacing: 4px; color: var(--white); line-height: 1;
  }
  .report-subtitle {
    position: absolute; left: 592px; top: 712px;
    font-family: "Roboto Slab", serif; font-weight: 700;
    font-size: 9px; letter-spacing: 2.6px; color: var(--grey-light);
  }

  .brand-name {
    position: absolute; left: 846px; top: 588px;
    font-family: "Montserrat", sans-serif; font-weight: 400;
    font-size: 15px; line-height: 1.2; letter-spacing: .3px;
    color: var(--ink-dark); white-space: nowrap;
  }
</style>
</head>
<body>
  <div class="spread">
    <svg class="spread-art" width="1116" height="800" viewBox="0 0 1116 800">
      <defs>
        <linearGradient id="photoTone" x1="0" y1="0" x2="1" y2="1">
          <stop offset="0" stop-color="#8a8a8a"/>
          <stop offset="0.5" stop-color="#b9b9b9"/>
          <stop offset="1" stop-color="#4e4e4e"/>
        </linearGradient>
        <linearGradient id="darkBand" x1="0" y1="0" x2="1" y2="0">
          <stop offset="0" stop-color="#4a4a4a"/>
          <stop offset="1" stop-color="#2e2e2e"/>
        </linearGradient>
      </defs>

      <g role="img" aria-label="Black and white photograph of schoolchildren at a rally, one holding a hand-drawn peace sign">
        <rect x="280" y="162" width="836" height="402" fill="url(#photoTone)"/>
      </g>

      <!-- back cover shapes -->
      <polygon points="330,564 558,470 558,564" fill="var(--grey-mid)" opacity=".85"/>
      <polygon points="280,564 558,520 558,800 280,800" fill="url(#darkBand)"/>
      <polygon points="0,490 548,800 0,800" fill="var(--green)"/>
      <polygon points="280,564 558,564 558,520" fill="var(--grey-deep)"/>

      <!-- front cover shapes -->
      <polygon points="558,522 800,627 1116,785 1116,800 558,800" fill="url(#darkBand)"/>
      <polygon points="558,470 800,627 558,522" fill="var(--grey-mid)"/>
      <polygon points="1116,427 1116,690 800,627" fill="var(--paper)"/>
      <polygon points="800,627 1116,690 1116,785" fill="var(--grey-light)"/>
      <polygon points="558,564 558,800 1116,800 1116,785" fill="#393939" opacity=".6"/>

      <!-- spine -->
      <rect x="556" y="0" width="4" height="800" fill="rgba(0,0,0,0.06)"/>
    </svg>

    <div class="contact">
      <p class="contact-title">CONTACT</p>
      <p class="contact-lines">Headquarters<br>Office of Digital Reachworks<br>1820 Larkmoor Lane #207-118<br>Brenton Falls, QX 40917</p>
      <p class="contact-lines">Phone: 555 014 2290<br>Email us: contact@qelvantrix.org</p>
    </div>
    <p class="contact-web">www.qelvantrix.org</p>

    <p class="brand-name">Office of Digital Reachworks</p>

    <h1 class="report-title">REPORT</h1>
    <p class="report-subtitle">OFFICE OF DIGITAL REACHWORKS</p>
  </div>
</body>
</html>
```